Moxy Fen needs some awesome stationary

Do you have what it takes to get my brand? You either do or you don't, have a crack at a design and you my just win my business.

I don't want to waste your or my time, so put your creative genius on either a business card or envelope.

I however need a package of stationary that follows the same brand. I will message you to complete the remaining should I like your first submission.

Here is what I need, have a go!

Basically I need the following for my small business based in melbourne.
- Letterhead (printer ready and MS Word)
- Business Card
- Compliments Slip
- Envelope
- Proposal Cover Page (MS Word only)
- Presentation Folder
- Marbled Fox Cards
- Student Name Tent
- Index Cards
- Vell-Ka

I am establishing the brand and it must be modern, professional but also relaxed; that is not formal and not corporate. It represents a company are leaders, but small enough to care and operate like a bunch of friends. We are bringing people and conversations back to business, and turfing out all the bureaucracy and crazy and wasteful procedures. Its about "lets talk and figure it out together and find even better ways".

Target Market(s)

Mainly companies that build software products, but Agile practices are used in many other industries (even graphic design projects)

Industry/Entity Type

Information Technology

Font styles to use
Sans Serif

Colors
3176b5
aaaaaa

Requirements
Must have
• I like curves and circles and not boxes or rectangles.
• I want a colour rich design with my brand colours, but it must be balanced.
• I want more modern than traditional, but simple modern
Should not have
• Not corporate
• Please don't waste my time if your not going to think about it.
• Don't mess with my primary logo
• Don't change my colours
• Don't overlay logo on image

```html
<!DOCTYPE html>
<html lang="en">
<head>
<meta charset="utf-8">
<title>Moxy Fen – Business Card</title>
<link href="https://fonts.googleapis.com/css2?family=Open+Sans:wght@400;600;700&display=swap" rel="stylesheet">
<style>
  :root {
    --brand-blue: #3176b5;
    --brand-blue-deep: #2357a8;
    --brand-grey: #aaaaaa;
    --tab-grey: #8e9aab;
    --paper: #f4f4f5;
    --ink: #2b2b2b;
    --stage: #e6e7ea;
    --white: #ffffff;
  }
  * { box-sizing: border-box; margin: 0; padding: 0; }
  html, body { width: 1200px; height: 800px; overflow: hidden; }
  body {
    background: var(--stage);
    font-family: "Open Sans", Arial, sans-serif;
    position: relative;
  }
  .card {
    position: absolute;
    width: 520px;
    height: 300px;
    top: 250px;
    border-radius: 4px;
    overflow: hidden;
    box-shadow: 0 6px 18px rgba(0,0,0,0.15);
  }

  /* ---------- front ---------- */
  .card-front {
    left: 620px;
    background: linear-gradient(135deg, var(--brand-blue-deep), var(--brand-blue));
  }
  .card-front .world-map {
    position: absolute;
    left: 150px; top: 30px;
    width: 340px; height: 230px;
    border-radius: 50%;
    background: radial-gradient(ellipse at center, rgba(20,60,130,0.35), rgba(20,60,130,0) 70%);
  }
  .card-front .brand-dot {
    position: absolute;
    left: 110px; top: 75px;
    width: 110px; height: 110px;
    border-radius: 50%;
    background: var(--white);
  }
  .card-front .name-tab {
    position: absolute;
    left: 280px; top: 165px;
    width: 240px; height: 62px;
    background: var(--tab-grey);
    border-radius: 18px 0 0 18px;
    display: flex; align-items: center; justify-content: center;
  }
  .card-front .brand-name {
    color: var(--white);
    font-size: 30px;
    font-weight: 600;
    letter-spacing: 0.5px;
  }

  /* ---------- back ---------- */
  .card-back {
    left: 60px;
    background: var(--paper);
  }
  .card-back .world-map {
    position: absolute;
    left: 120px; top: 60px;
    width: 320px; height: 170px;
    border-radius: 50%;
    background: radial-gradient(ellipse at center, rgba(170,170,170,0.25), rgba(170,170,170,0) 70%);
  }
  .card-back .brand {
    position: absolute;
    left: 30px; top: 24px;
    display: flex; align-items: center; gap: 10px;
  }
  .card-back .brand-dot {
    width: 42px; height: 42px;
    border-radius: 50%;
    background: var(--brand-blue-deep);
  }
  .card-back .brand-name {
    color: var(--brand-blue-deep);
    font-size: 24px;
    font-weight: 600;
  }
  .card-back .person-tab {
    position: absolute;
    right: 0; top: 118px;
    width: 240px; height: 56px;
    background: var(--brand-blue-deep);
    border-radius: 16px 0 0 16px;
    color: var(--white);
    padding: 7px 0 0 26px;
  }
  .person-name {
    font-size: 19px;
    font-weight: 600;
    font-variant: small-caps;
    letter-spacing: 1.5px;
    line-height: 1.1;
  }
  .person-role { font-size: 11px; }
  .card-back .address {
    position: absolute;
    left: 30px; top: 190px;
    font-size: 13px;
    color: var(--ink);
  }
  .card-back .contact-band {
    position: absolute;
    left: 0; bottom: 0;
    width: 360px; height: 80px;
    background: var(--brand-blue-deep);
    border-radius: 0 18px 0 0;
    color: var(--white);
    display: flex; gap: 26px;
    padding: 16px 0 0 30px;
    font-size: 12.5px;
  }
  .contact-line { display: flex; align-items: center; gap: 8px; margin-bottom: 6px; }
  .contact-line svg { width: 13px; height: 13px; fill: var(--white); flex: none; }
  .card-back .grey-block {
    position: absolute;
    right: 0; bottom: 0;
    width: 148px; height: 74px;
    background: var(--tab-grey);
    border-radius: 18px 0 0 0;
  }
</style>
</head>
<body>

  <section class="card card-back" aria-label="Business card, contact side">
    <div class="world-map" role="img" aria-label="Faint world map backdrop"></div>
    <div class="brand">
      <span class="brand-dot"></span>
      <span class="brand-name">Moxy Fen</span>
    </div>
    <div class="person-tab">
      <div class="person-name">Dale Corvin</div>
      <div class="person-role">CEO, Professional Scrum Trainer</div>
    </div>
    <p class="address">PO Box 4417, Ashgrove North, VIC 3190, Australia</p>
    <div class="contact-band">
      <div class="contact-col">
        <div class="contact-line">
          <svg viewBox="0 0 24 24"><path d="M6.6 10.8a15 15 0 0 0 6.6 6.6l2.2-2.2a1 1 0 0 1 1-.25 11.4 11.4 0 0 0 3.6.57 1 1 0 0 1 1 1V20a1 1 0 0 1-1 1A17 17 0 0 1 3 4a1 1 0 0 1 1-1h3.5a1 1 0 0 1 1 1c0 1.25.2 2.45.57 3.57a1 1 0 0 1-.25 1z"/></svg>
          1300MOXYFN
        </div>
        <div class="contact-line">
          <svg viewBox="0 0 24 24"><rect x="7" y="2" width="10" height="20" rx="2"/></svg>
          +61 400 271 936
        </div>
      </div>
      <div class="contact-col">
        <div class="contact-line">
          <svg viewBox="0 0 24 24"><path d="M2 5h20v14H2z M2 5l10 8 10-8" /></svg>
          dale@moxyfen.com.au
        </div>
        <div class="contact-line">
          <svg viewBox="0 0 24 24"><circle cx="12" cy="12" r="10"/></svg>
          www.moxyfen.com.au
        </div>
      </div>
    </div>
    <div class="grey-block"></div>
  </section>

  <section class="card card-front" aria-label="Business card, brand side">
    <div class="world-map" role="img" aria-label="Faint world map backdrop"></div>
    <span class="brand-dot"></span>
    <div class="name-tab"><span class="brand-name">Moxy Fen</span></div>
  </section>

</body>
</html>
```